Frozen Yogurt "Now Open" Postcard

I would like to see a very fun, vibrant postcard design that will catch people's attention when going through their mail. It will be an announcement that the store is "Now Open". Please refer to the website... www.tundracups.com for details and design inspiration. Include the phone, address (with mini map), and website info.

Use Jumbo Postcard size... 11" x 6"

Target Market(s)

Women, kids and families

Industry/Entity Type

Food Store

Colors
0692cd
e34298
b768aa

Requirements
Must have
• Phone, Web address, mailing address (with map). Vibrant colors, delicious looking frozen yogurt.

```html
<!DOCTYPE html>
<html lang="en">
<head>
<meta charset="utf-8">
<title>Tundra Cups – Now Open Postcard</title>
<link href="https://fonts.googleapis.com/css2?family=Open+Sans:wght@300;400;600;800&display=swap" rel="stylesheet">
<style>
  :root{
    --pink:#e34298;
    --magenta:#d61f7a;
    --purple:#b768aa;
    --violet:#9b59b6;
    --teal:#2aa6b8;
    --mint:#7cc4b0;
    --blue:#0692cd;
    --ink:#1d1d1d;
    --paper:#ffffff;
    --stage:#1b1b1b;
    --cream:#f1ecc8;
  }
  *{box-sizing:border-box;margin:0;padding:0}
  html,body{width:1200px;height:864px;overflow:hidden;background:var(--stage);font-family:"Open Sans",sans-serif}
  .card{position:absolute;left:230px;width:740px;height:404px;background:var(--paper);overflow:hidden}
  .card--front{top:20px}
  .card--back{top:444px}

  /* front */
  .front-photo{position:absolute;left:40px;top:0;width:300px;height:220px;
    background:radial-gradient(ellipse at 55% 40%,#f7a7c4 0%,#f28bb0 40%,#fbe3ec 75%,#ffffff 100%)}
  .front-wave{position:absolute;left:0;top:0;width:740px;height:404px}
  .decor{position:absolute;border-radius:50%}
  .decor--top{left:420px;top:-20px;width:110px;height:110px;background:radial-gradient(circle,#fff 0 22%,var(--pink) 23% 100%);opacity:.9}
  .decor--big{left:560px;top:210px;width:240px;height:240px;background:radial-gradient(circle,#fff 0 18%,var(--mint) 19% 60%,var(--purple) 61% 100%)}
  .dot{position:absolute;width:10px;height:10px;border-radius:50%}
  .dot--teal{background:var(--teal)}
  .dot--cream{background:var(--cream);width:14px;height:14px}
  .dot--pink{background:var(--pink);width:8px;height:8px}
  .brand{position:absolute;left:400px;top:110px;width:260px;text-align:center}
  .brand-name{font-weight:800;font-size:50px;line-height:1;color:var(--pink);letter-spacing:-1px}
  .brand-tag{margin-top:6px;font-weight:400;font-size:15px;letter-spacing:2px;color:var(--teal)}
  .headline{position:absolute;left:390px;top:240px;font-weight:300;font-size:40px;letter-spacing:3px;color:var(--ink)}

  /* back */
  .store-photo{position:absolute;left:0;top:0;width:370px;height:404px;
    background:linear-gradient(180deg,#e9dcc8 0%,#f1ece4 35%,#c9e3ea 70%,#eef2f4 100%)}
  .info{position:absolute;left:370px;top:0;right:0;bottom:0}
  .loc-label{position:absolute;left:18px;top:12px;font-size:13px;font-weight:600;color:var(--ink)}
  .map{position:absolute;left:18px;top:34px;width:150px;height:100px;background:linear-gradient(135deg,#e6e6e6,#d3d3d3)}
  .address{position:absolute;left:185px;top:68px;display:flex;gap:8px;align-items:flex-start}
  .address p{font-size:12px;font-weight:600;line-height:1.3;color:var(--ink)}
  .contact{position:absolute;left:0;width:300px;text-align:center;font-size:14px;color:var(--ink)}
  .contact svg{display:block;margin:0 auto 4px}
  .contact--phone{top:160px}
  .contact--mail{top:228px}
  .contact--web{top:296px}
  .icon{width:20px;height:20px}
  .decor--back{left:255px;top:150px;width:130px;height:130px;background:radial-gradient(circle,#fff 0 20%,var(--mint) 21% 100%)}
  .decor--back-top{left:200px;top:28px;width:44px;height:44px;background:radial-gradient(circle,#fff 0 30%,var(--teal) 31% 100%)}
  .social-band{position:absolute;left:0;right:0;bottom:0;height:54px;
    background:linear-gradient(90deg,var(--magenta),var(--purple));display:flex;justify-content:center;align-items:center;gap:14px}
  .social-band span{width:26px;height:26px;border-radius:50%;background:var(--paper)}
</style>
</head>
<body>

<section class="card card--front" aria-label="Postcard front">
  <div class="front-photo" role="img" aria-label="Photo of strawberry frozen yogurt swirl with fresh strawberries and mint"></div>
  <svg class="front-wave" viewBox="0 0 740 404" aria-hidden="true">
    <defs>
      <linearGradient id="waveFill" x1="0" y1="0" x2="1" y2="1">
        <stop offset="0" stop-color="#d61f7a"/>
        <stop offset="1" stop-color="#b768aa"/>
      </linearGradient>
    </defs>
    <path d="M0 190 C120 200 260 210 330 270 C380 320 400 370 420 404 L0 404 Z" fill="#2aa6b8"/>
    <path d="M0 205 C110 215 240 230 305 285 C350 330 370 370 385 404 L0 404 Z" fill="url(#waveFill)"/>
  </svg>
  <div class="decor decor--top" role="img" aria-label="Decorative swirl"></div>
  <div class="decor decor--big" role="img" aria-label="Decorative swirl"></div>
  <span class="dot dot--teal" style="left:360px;top:30px"></span>
  <span class="dot dot--pink" style="left:350px;top:110px"></span>
  <span class="dot dot--cream" style="left:700px;top:120px"></span>
  <span class="dot dot--teal" style="left:670px;top:210px"></span>
  <span class="dot dot--cream" style="left:370px;top:190px"></span>
  <span class="dot dot--pink" style="left:660px;top:80px"></span>
  <span class="dot dot--teal" style="left:530px;top:205px"></span>

  <div class="brand">
    <p class="brand-name">Tundra Cups</p>
    <p class="brand-tag">FROZEN YOGURT</p>
  </div>
  <h1 class="headline">NOW OPEN</h1>
</section>

<section class="card card--back" aria-label="Postcard back">
  <div class="store-photo" role="img" aria-label="Photo of the store interior with a round counter, yogurt machines and toppings wall"></div>
  <div class="info">
    <p class="loc-label">Location :</p>
    <div class="map" role="img" aria-label="Mini map showing the store location"></div>
    <div class="decor decor--back-top" role="img" aria-label="Decorative swirl"></div>
    <div class="address">
      <svg class="icon" viewBox="0 0 20 20" aria-hidden="true"><circle cx="10" cy="10" r="10" fill="#b768aa"/><path d="M10 4a3.5 3.5 0 0 0-3.5 3.5C6.5 10 10 15 10 15s3.5-5 3.5-7.5A3.5 3.5 0 0 0 10 4z" fill="#fff"/><circle cx="10" cy="7.5" r="1.3" fill="#b768aa"/></svg>
      <p>1200 Maple Grove Way<br>Brookfield, CA<br>90000</p>
    </div>
    <div class="decor decor--back" role="img" aria-label="Decorative swirl"></div>
    <p class="contact contact--phone">
      <svg class="icon" viewBox="0 0 20 20" aria-hidden="true"><circle cx="10" cy="10" r="10" fill="#e34298"/><path d="M7 5l2 2-1 1.5c.6 1.3 1.5 2.2 2.8 2.8L12.3 10l2 2-1.3 1.7C9.5 13.5 6.5 10.5 6.3 6.3z" fill="#fff"/></svg>
      555.010.0190
    </p>
    <p class="contact contact--mail">
      <svg class="icon" viewBox="0 0 20 20" aria-hidden="true"><circle cx="10" cy="10" r="10" fill="#e34298"/><rect x="5" y="6.5" width="10" height="7" fill="#fff"/><path d="M5 6.5l5 4 5-4" fill="none" stroke="#e34298" stroke-width="1"/></svg>
      info@tundracups.com
    </p>
    <p class="contact contact--web">
      <svg class="icon" viewBox="0 0 20 20" aria-hidden="true"><circle cx="10" cy="10" r="10" fill="#b768aa"/><circle cx="10" cy="10" r="5" fill="none" stroke="#fff" stroke-width="1.2"/><path d="M5 10h10M10 5c-2 3-2 7 0 10M10 5c2 3 2 7 0 10" fill="none" stroke="#fff" stroke-width="1"/></svg>
      www.tundracups.com
    </p>
    <span class="dot dot--pink" style="left:10px;top:150px"></span>
    <span class="dot dot--teal" style="left:30px;top:225px"></span>
    <span class="dot dot--cream" style="left:90px;top:300px"></span>
    <span class="dot dot--cream" style="left:320px;top:110px"></span>
    <span class="dot dot--teal" style="left:240px;top:285px"></span>
    <div class="social-band" aria-label="Social media">
      <span></span><span></span><span></span>
    </div>
  </div>
</section>

</body>
</html>
```